Design a single page Shopify store web page

We are looking to have a page designed for a single page Shopify store with 2 products. We already have a basic structure that we like, though we are open to suggestions. We are looking for somebody to provide a design/color scheme that we can then implement using Shopify's templating system. We can handle the implementation(HTML / CSS / jS) as we already have 2 web developers on the team, but have not been able to find a design we liked.

The job would consist of providing a mockup (photoshop or otherwise) and any vector graphics you choose to create for the site (we can provide product photos and other images).

You can also look at http://brickdune.com.au for some of our design direction we have used so far

Target Market(s)

Young Australian Males (18 - 49)

Industry/Entity Type

Store

Number of Pages Required

1 page

Font styles to use
Serif
Sans Serif

Requirements
Must have
• Single Page Design
• E-commerce Product Purchase
• Manly (whatever interpretation of that you have)

```html
<!DOCTYPE html>
<html lang="en">
<head>
<meta charset="utf-8">
<title>Brick Dune – Underwear and Socks Plans</title>
<link rel="stylesheet" href="https://fonts.googleapis.com/css2?family=Nunito+Sans:wght@200;300;400;600;700;800&display=swap">
<style>
:root{
  --ink:#222222;
  --header:#232323;
  --sky:#00adef;
  --sky-light:#5cd0ff;
  --card:#0c95d3;
  --btn:#12b5f3;
  --green:#5cb85c;
  --white:#ffffff;
  --grey:#6a6a6a;
  --rule:#d6d6d6;
  --garment:#1c1c1c;
}
*{margin:0;padding:0;box-sizing:border-box}
html,body{width:1200px;height:2184px;overflow:hidden}
body{font-family:"Nunito Sans",Arial,sans-serif;color:var(--ink);background:var(--white);position:relative}

/* header */
.site-header{position:absolute;left:0;top:0;width:1200px;height:112px;background:var(--header)}
.brand{position:absolute;left:32px;top:24px;display:flex;align-items:center;gap:16px}
.brand-mark{width:58px;height:62px;border:2px solid #cfcfcf;border-radius:50%}
.brand-name{font-size:52px;font-weight:300;color:#d0d0d0;letter-spacing:3px;text-transform:uppercase;line-height:1}
.main-nav{position:absolute;top:44px;left:762px;display:flex;gap:44px}
.main-nav a{color:var(--white);font-size:18px;text-decoration:none}

/* hero */
.hero{position:absolute;left:0;top:112px;width:1200px;height:433px;
  background:radial-gradient(ellipse 420px 260px at 600px 150px,var(--sky-light),var(--sky) 80%)}
.hero-title{position:absolute;left:0;width:1200px;top:68px;text-align:center;font-size:61px;font-weight:200;color:var(--white);letter-spacing:1px}
.hero-sub{position:absolute;left:0;width:1200px;top:158px;text-align:center;font-size:27px;font-weight:400;color:var(--ink)}
.hero-freq{position:absolute;left:0;width:1200px;top:208px;text-align:center;font-size:44px;font-weight:800;color:var(--white)}
.btn-subscribe{position:absolute;left:489px;top:297px;width:220px;height:72px;border:2px solid #1c4a60;
  color:#1c3e52;font-size:28px;font-weight:700;display:flex;align-items:center;justify-content:center;letter-spacing:1px}
.slider-dots{position:absolute;left:565px;top:398px;display:flex;gap:14px}
.slider-dots span{width:12px;height:12px;border-radius:50%;background:#9fe0fb}
.slider-dots span.active{background:var(--white)}
.product-shot{position:absolute;background:linear-gradient(160deg,#3a3a3a,var(--garment))}
.shot-briefs{left:22px;top:178px;width:277px;height:200px;border-radius:10px 10px 40px 40px}
.shot-sock{left:878px;top:190px;width:242px;height:214px;border-radius:30px 60px 40px 100px;background:linear-gradient(160deg,#333,#111 60%,#7a7a7a)}

/* section titles */
.section-title{position:absolute;left:0;width:1200px;text-align:center;font-weight:700;text-transform:uppercase}

/* how it works */
.step{position:absolute;width:300px;text-align:center}
.step-icon{width:169px;height:169px;border-radius:50%;background:var(--garment);margin:0 auto;display:flex;align-items:center;justify-content:center}
.step-title{margin-top:25px;font-size:26px;font-weight:600;text-transform:uppercase}
.step-text{margin:10px auto 0;width:240px;font-size:14px;line-height:20px;color:var(--grey)}

/* plans */
.plans{position:absolute;left:0;top:1034px;width:1200px;height:588px;background:var(--sky)}
.plan-card{position:absolute;top:140px;width:498px;height:378px;background:var(--card)}
.plan-name{position:absolute;left:0;top:22px;width:498px;text-align:center;font-size:27px;font-weight:600;color:var(--ink)}
.plan-photo{position:absolute;left:28px;top:79px;width:256px;height:256px}
.photo-briefs{background:linear-gradient(135deg,#d9d9d9,#a9a9a9 60%,#8a8a8a)}
.photo-socks{background:linear-gradient(160deg,#3b3b3b,#7b5a40 55%,#9a8f80)}
.plan-link{position:absolute;left:326px;width:128px;height:42px;background:var(--btn);color:var(--white);
  font-size:14px;font-weight:700;display:flex;align-items:center;justify-content:center}
.plan-price{position:absolute;left:300px;width:160px;top:190px;text-align:right;font-size:44px;font-weight:700;color:var(--ink)}
.btn-get{position:absolute;left:317px;top:258px;width:136px;height:72px;background:var(--green);color:var(--white);
  font-size:27px;font-weight:600;display:flex;align-items:center;justify-content:center}

/* faq */
.faq-grid{position:absolute;left:157px;top:1754px;width:883px;height:280px}
.faq-item{position:absolute;width:294px;text-align:center}
.faq-q{font-size:17px;font-weight:600;text-transform:uppercase;line-height:20px;height:40px;display:flex;align-items:center;justify-content:center}
.faq-a{margin:8px auto 0;width:230px;font-size:13px;line-height:20px;color:var(--grey)}
.faq-rule-h{position:absolute;left:0;top:140px;width:883px;height:1px;background:var(--rule)}
.faq-rule-v{position:absolute;top:0;width:1px;height:280px;background:var(--rule)}

/* footer */
.site-footer{position:absolute;left:0;top:2075px;width:1200px;height:109px;background:var(--header);color:var(--white);font-size:16px}
.footer-links{position:absolute;left:89px;top:43px}
.footer-email{position:absolute;left:470px;top:43px}
.social{position:absolute;top:41px;width:31px;height:31px;border-radius:3px}
.pay{position:absolute;top:45px;width:36px;height:22px;background:var(--white);border-radius:2px;color:var(--ink);
  font-size:8px;font-weight:700;display:flex;align-items:center;justify-content:center}
</style>
</head>
<body>

<header class="site-header">
  <div class="brand"><span class="brand-mark"></span><span class="brand-name">Brick Dune</span></div>
  <nav class="main-nav"><a href="#how">How It Works</a><a href="#plans">Plans</a><a href="#faq">FAQ</a><a href="#about">About us</a></nav>
</header>

<section class="hero">
  <div class="product-shot shot-briefs" role="img" aria-label="Black boxer briefs product photo"></div>
  <div class="product-shot shot-sock" role="img" aria-label="Black and grey ankle sock product photo"></div>
  <h1 class="hero-title">NEW UNDERWEAR AND SOCKS</h1>
  <p class="hero-sub">DELIVERED TO YOUR DOOR</p>
  <p class="hero-freq">EVERY 3 OR 6 MONTHS</p>
  <a class="btn-subscribe">SUBSRIBE</a>
  <div class="slider-dots"><span></span><span class="active"></span><span></span></div>
</section>

<section id="how">
  <h2 class="section-title" style="top:583px;font-size:35px">How It Works</h2>
  <div class="step" style="left:134px;top:678px">
    <div class="step-icon"><svg width="80" height="100" viewBox="0 0 80 100"><circle cx="30" cy="22" r="14" fill="none" stroke="#fff" stroke-width="6"/><circle cx="30" cy="22" r="5" fill="#fff"/><path d="M24 30 V70 L14 60 Q8 56 6 64 L26 92 H64 Q72 80 70 62 V52 Q70 46 63 46 Q58 40 52 44 Q48 38 42 42 V30 Q42 24 33 24 Q24 24 24 30Z" fill="#fff"/></svg></div>
    <h3 class="step-title">Choose a Plan</h3>
    <p class="step-text">Sed ut perspiciatis unde omnis iste natus error sit voluptatem accusan-tium doloremque</p>
  </div>
  <div class="step" style="left:451px;top:678px">
    <div class="step-icon"><svg width="70" height="100" viewBox="0 0 70 100"><path d="M8 30 Q8 4 35 4 Q62 4 62 28 Q62 42 48 50 Q42 54 42 64 H26 Q26 48 38 40 Q46 35 46 28 Q46 19 35 19 Q24 19 24 30Z" fill="#fff"/><circle cx="34" cy="84" r="10" fill="#fff"/></svg></div>
    <h3 class="step-title">Choose How Often</h3>
    <p class="step-text">Sed ut perspiciatis unde omnis iste natus error sit voluptatem accusan-tium doloremque</p>
  </div>
  <div class="step" style="left:762px;top:678px">
    <div class="step-icon"><svg width="100" height="90" viewBox="0 0 100 90"><path d="M4 10 H20 L34 60 H84" fill="none" stroke="#fff" stroke-width="8" stroke-linejoin="round"/><path d="M24 22 H94 L84 52 H32Z" fill="#fff"/><circle cx="40" cy="74" r="9" fill="none" stroke="#fff" stroke-width="6"/><circle cx="80" cy="74" r="9" fill="none" stroke="#fff" stroke-width="6"/></svg></div>
    <h3 class="step-title">Get Your Pack</h3>
    <p class="step-text">Sed ut perspiciatis unde omnis iste natus error sit voluptatem accusan-tium doloremque</p>
  </div>
</section>

<section class="plans" id="plans">
  <h2 class="section-title" style="top:64px;font-size:32px;color:var(--white)">Plans</h2>
  <article class="plan-card" style="left:92px">
    <h3 class="plan-name">COMPORT</h3>
    <div class="plan-photo photo-briefs" role="img" aria-label="Model wearing white briefs"></div>
    <a class="plan-link" style="top:79px">VIEW DETAILS</a>
    <a class="plan-link" style="top:131px">COLLECTIONS</a>
    <p class="plan-price">$30</p>
    <a class="btn-get">GET IT!</a>
  </article>
  <article class="plan-card" style="left:610px">
    <h3 class="plan-name">COMPORT</h3>
    <div class="plan-photo photo-socks" role="img" aria-label="Brown leather shoes with bright coloured socks"></div>
    <a class="plan-link" style="top:79px">VIEW DETAILS</a>
    <a class="plan-link" style="top:131px">COLLECTIONS</a>
    <p class="plan-price">$30</p>
    <a class="btn-get">GET IT!</a>
  </article>
</section>

<section id="faq">
  <h2 class="section-title" style="top:1670px;font-size:33px">FAQ</h2>
  <div class="faq-grid">
    <div class="faq-rule-h"></div>
    <div class="faq-rule-v" style="left:281px"></div>
    <div class="faq-rule-v" style="left:609px"></div>
    <div class="faq-item" style="left:-13px;top:0"><h4 class="faq-q">What is Brick Dune?</h4><p class="faq-a">Sed ut perspiciatis unde omnis iste natus error sit voluptatem accusantium doloremque laudantium.</p></div>
    <div class="faq-item" style="left:298px;top:0"><h4 class="faq-q">What is your<br>satisfaction gurantee?</h4><p class="faq-a">Sed ut perspiciatis unde omnis iste natus error sit voluptatem accusantium doloremque laudantium.</p></div>
    <div class="faq-item" style="left:614px;top:0"><h4 class="faq-q">Shipping Policy</h4><p class="faq-a">Sed ut perspiciatis unde omnis iste natus error sit voluptatem accusantium doloremque laudantium.</p></div>
    <div class="faq-item" style="left:-13px;top:155px"><h4 class="faq-q">Dune Plan?</h4><p class="faq-a">Sed ut perspiciatis unde omnis iste natus error sit voluptatem accusantium doloremque laudantium.</p></div>
    <div class="faq-item" style="left:298px;top:155px"><h4 class="faq-q">Return Policy</h4><p class="faq-a">Sed ut perspiciatis unde omnis iste natus error sit voluptatem accusantium doloremque laudantium.</p></div>
    <div class="faq-item" style="left:614px;top:155px"><h4 class="faq-q">What brands do you<br>stock?</h4><p class="faq-a">Sed ut perspiciatis unde omnis iste natus error sit voluptatem accusantium doloremque laudantium.</p></div>
  </div>
</section>

<footer class="site-footer">
  <p class="footer-links">Shipping / Return / Payment / Terms/Privacy</p>
  <p class="footer-email">holla@brickdune.com.au</p>
  <span class="social" style="left:702px;background:#f0b323"></span>
  <span class="social" style="left:750px;background:#5bb6e0"></span>
  <span class="social" style="left:801px;background:#d85e91"></span>
  <span class="social" style="left:850px;background:#3b5998"></span>
  <span class="pay" style="left:955px">VELA</span>
  <span class="pay" style="left:1000px">MERIT</span>
  <span class="pay" style="left:1046px">DISKO</span>
</footer>

</body>
</html>
```